900mm double sided Card Ponytail Insert for hair

I need print ready file designs for card packaging inserts for my line of ponytails, These are two sided colour and fold at each end or contain the hair, for structure and so the brand is on display. These will be marketed as luxury ponytails, so we want a simple, soft but luxurious design feel. All the details are below but it will be the logo, photos and simple messaging

Target Market(s)

18-30 females

Industry/Entity Type

Beauty

Font styles to use
Serif

Requirements
Must have
• - Velmora Logo on the back and top front fold.
'Luxury Synthetic Ponytails' Head line
'For effortlessly long and luxurious hair' tag line
'For tutorials, questions and inspiration head to our 'Glow Corner' on velmorabeauty.com'
www.velmorabeauty.com
Tag us on socials! @velmorabeautyofficial (instagram and Facebook logos)
3 step-by-step pictures (holding pictures please until i have some taken)
Nice to have
• (notes to designers) view our website to see our branding velmorabeauty.com - it would be good to use our brand colours and somekind of tropical leaves maybe? i'm thinking palm leaves?
- my brand font is Sweet Getaway - but this may only be good for the biggest headings

```html
<!DOCTYPE html>
<html lang="en">
<head>
<meta charset="utf-8">
<title>Velmora Beauty – Ponytail Card Insert</title>
<link rel="stylesheet" href="https://fonts.googleapis.com/css2?family=Lora:wght@400;600&family=Sacramento&display=swap">
<style>
  :root{
    --teal:#6cc4b1;
    --gold:#d89c46;
    --gold-soft:#e3a94f;
    --cream:#fcf9f4;
    --kraft:#f5e8c4;
    --ink:#4a4a4a;
    --page:#ffffff;
    --serif:"Lora", Georgia, serif;
    --script:"Sacramento", cursive;
  }
  *{box-sizing:border-box;margin:0;padding:0}
  html,body{width:1200px;height:2556px;overflow:hidden;background:var(--page)}
  body{position:relative;font-family:var(--serif);color:var(--ink)}
  .abs{position:absolute}
  .center{text-align:center}

  .panel{position:absolute;background:var(--cream)}
  .panel-front{left:130px;top:185px;width:325px;height:2180px;border-left:45px solid var(--gold)}
  .front-middle{left:175px;top:690px;width:280px;height:1400px;background:var(--kraft)}
  .panel-back{left:625px;top:170px;width:295px;height:2200px;border-left:15px solid var(--gold);border-right:20px solid var(--gold)}
  .fold-line{position:absolute;height:0;border-top:1px dashed #e58b8b}

  .brand{position:absolute;text-align:center;font-family:var(--serif);font-weight:400;color:var(--gold);letter-spacing:2px;white-space:nowrap}
  .brand .dot{display:inline-block;width:10px;height:10px;border-radius:50%;background:var(--teal);margin-right:8px;vertical-align:middle}
  .brand-sub{position:absolute;text-align:center;font-family:var(--serif);color:#555;white-space:nowrap}

  .headline{position:absolute;text-align:center;font-family:var(--script);color:var(--gold);white-space:nowrap}
  .divider{position:absolute;height:0;border-top:1px solid var(--teal)}

  .photo{position:absolute}
  .tag-band{position:absolute;background:var(--teal);color:#fff;font-size:15px;line-height:20px;padding:6px 0 0 22px;border-radius:28px 0 0 28px}

  .styles-box{left:658px;top:778px;width:222px;height:204px;background:var(--teal);color:#fff;text-align:center}
  .styles-box .small{font-size:18px;padding-top:22px}
  .styles-box .big{font-size:48px;line-height:54px}
  .styles-box .and{font-size:17px;line-height:18px}
  .step-band{left:638px;top:1022px;width:262px;height:110px;background:var(--teal)}
  .step{position:absolute;top:1040px;width:69px;height:68px;border:1px solid #fff}
  .step-label{position:absolute;top:1112px;width:69px;font-size:10px;line-height:14px;color:#fff;text-align:center}
  .frame{position:absolute;border:1px solid var(--teal)}

  .reviews-title{left:640px;top:1665px;width:260px;font-size:58px}
  .review{position:absolute;left:668px;width:200px;font-size:10px;line-height:13.6px;text-align:justify;color:#555}
  .review h3{font-size:11.5px;font-weight:600;color:var(--gold-soft);margin-bottom:2px;text-align:left}
  .note-box{left:668px;top:2022px;width:200px;height:58px;border:1px solid var(--teal);font-size:10px;line-height:14px;text-align:center;padding:7px 6px 0}
  .url{color:#444;white-space:nowrap}
  .follow{left:640px;top:2158px;width:260px;font-size:17px;color:var(--teal)}
  .social{position:absolute;top:2192px;width:40px;height:40px;border-radius:50%;background:var(--teal)}
  .handle{left:640px;top:2240px;width:260px;font-size:14px;white-space:nowrap}
  .refund{left:668px;top:2275px;width:200px;height:63px;background:var(--teal);color:#fff;font-size:10px;line-height:14px;text-align:center;padding-top:10px}
  .refund b{font-weight:600}
</style>
</head>
<body>

<!-- Front of insert -->
<section class="panel panel-front" aria-label="Front of insert"></section>
<div class="abs front-middle"></div>
<div class="fold-line" style="left:175px;top:218px;width:280px"></div>
<div class="fold-line" style="left:175px;top:2332px;width:280px"></div>

<div class="brand" style="left:175px;top:268px;width:280px;font-size:34px"><span class="dot"></span>Velmora</div>
<div class="brand-sub" style="left:175px;top:314px;width:280px;font-size:10px;letter-spacing:9px">BEAUTY</div>
<div class="divider" style="left:218px;top:346px;width:178px"></div>
<div class="headline" style="left:175px;top:352px;width:280px;font-size:32px">luxury synthetic ponytails</div>
<div class="divider" style="left:218px;top:398px;width:178px"></div>
<div class="photo" role="img" aria-label="Model with long blonde balayage hair wearing a grey check top" style="left:185px;top:410px;width:270px;height:270px;background:linear-gradient(180deg,#efe9e1 0%,#d9c3a6 45%,#9a9491 100%);border-radius:0 0 40px 120px"></div>
<div class="tag-band" style="left:235px;top:572px;width:220px;height:54px">For effortlessly long<br>and luxurious hair</div>

<div class="brand" style="left:175px;top:2150px;width:280px;font-size:30px"><span class="dot"></span>Velmora</div>
<div class="brand-sub" style="left:175px;top:2192px;width:280px;font-size:9px;letter-spacing:9px">BEAUTY</div>
<div class="divider" style="left:218px;top:2224px;width:178px"></div>
<div class="headline" style="left:175px;top:2226px;width:280px;font-size:30px">luxury synthetic ponytails</div>
<div class="divider" style="left:218px;top:2270px;width:178px"></div>
<div class="abs center url" style="left:175px;top:2293px;width:280px;font-size:14px">www.velmorabeauty.com</div>

<!-- Back of insert -->
<section class="panel panel-back" aria-label="Back of insert"></section>
<div class="fold-line" style="left:640px;top:172px;width:260px"></div>
<div class="fold-line" style="left:640px;top:2368px;width:260px"></div>

<div class="brand" style="left:640px;top:298px;width:260px;font-size:36px"><span class="dot"></span>Velmora</div>
<div class="brand-sub" style="left:640px;top:343px;width:260px;font-size:10px;letter-spacing:10px">BEAUTY</div>
<div class="divider" style="left:683px;top:420px;width:178px"></div>
<div class="headline" style="left:640px;top:432px;width:260px;font-size:32px">luxury synthetic ponytails</div>
<div class="divider" style="left:683px;top:481px;width:178px"></div>

<div class="photo" role="img" aria-label="Model with long ombré blonde hair in a grey check outfit" style="left:658px;top:557px;width:222px;height:221px;background:linear-gradient(180deg,#f2f2f2 0%,#c9b8a3 45%,#8d8b8c 100%)"></div>
<div class="abs styles-box">
  <div class="small">Comes in various</div>
  <div class="big">Styles</div>
  <div class="and">and</div>
  <div class="big">Colours</div>
</div>

<div class="abs step-band"></div>
<div class="step" role="img" aria-label="Step 1 photo placeholder: gathering the hair into a ponytail" style="left:658px;background:linear-gradient(180deg,#e8d3a0,#b89668)"></div>
<div class="step" role="img" aria-label="Step 2 photo placeholder: attaching the ponytail" style="left:735px;background:linear-gradient(180deg,#9aaec4,#5a6f8c)"></div>
<div class="step" role="img" aria-label="Step 3 photo placeholder: the finished ponytail" style="left:810px;background:linear-gradient(180deg,#7fe0dc,#2fb3b0)"></div>
<div class="step-label" style="left:658px">Step 1</div>
<div class="step-label" style="left:735px">Step 2</div>
<div class="step-label" style="left:810px">Step 3</div>

<div class="frame" style="left:658px;top:1165px;width:147px;height:215px"></div>
<div class="photo" role="img" aria-label="Long wavy silver ombré wig" style="left:662px;top:1170px;width:120px;height:205px;background:linear-gradient(180deg,#6e6e6e 0%,#c8c8c8 35%,#ebebeb 100%)"></div>
<div class="frame" style="left:785px;top:1172px;width:95px;height:96px"></div>
<div class="photo" role="img" aria-label="Model wearing silver wavy wig" style="left:786px;top:1173px;width:93px;height:94px;background:linear-gradient(180deg,#c9c3c3,#8f8a8a)"></div>
<div class="frame" style="left:785px;top:1275px;width:95px;height:95px"></div>
<div class="photo" role="img" aria-label="Model wearing silver wavy wig, smiling" style="left:786px;top:1276px;width:93px;height:93px;background:linear-gradient(180deg,#f3f3f3,#bdbdbd)"></div>

<div class="frame" style="left:658px;top:1423px;width:140px;height:214px"></div>
<div class="photo" role="img" aria-label="Long wavy pastel blue wig" style="left:662px;top:1428px;width:120px;height:204px;background:linear-gradient(180deg,#5a6c80 0%,#8fbde8 35%,#b7d6f2 100%)"></div>
<div class="frame" style="left:785px;top:1432px;width:95px;height:95px"></div>
<div class="photo" role="img" aria-label="Model wearing pastel blue wig on a street" style="left:786px;top:1433px;width:93px;height:93px;background:linear-gradient(180deg,#a9b8c6,#4b5d7a)"></div>
<div class="frame" style="left:785px;top:1534px;width:95px;height:95px"></div>
<div class="photo" role="img" aria-label="Model wearing pastel blue wig against a pink backdrop" style="left:786px;top:1535px;width:93px;height:93px;background:linear-gradient(180deg,#f0a3c4,#a9c3ee)"></div>

<div class="divider" style="left:680px;top:1667px;width:178px"></div>
<div class="headline reviews-title">reviews</div>
<div class="divider" style="left:680px;top:1742px;width:178px"></div>

<article class="review" style="top:1775px">
  <h3>LOVE IT!!</h3>
  I was sooo surprised at the quality of this wig! It's silky smooth. I customised a little with baby hairs and clipped it back with a clip to look like my usual style. People were so surprised that it wasn't my hair! 5 stars, highly recommend!
</article>
<article class="review" style="top:1897px">
  <h3>THE BEST WIG EVER!</h3>
  Since having chemotherapy and losing my hair I've become quite the wig collector. I've paid £300+ for some of my wigs but without a doubt this one is by far my favourite. It has a great hair line, so soft, it's the perfect length, gorgeous colour with a realistic shape and cut xx
</article>

<div class="abs note-box">For tutorials, questions and inspiration head to our ‘Glow Corner’ on velmorabeauty.com</div>
<div class="divider" style="left:680px;top:2090px;width:178px"></div>
<div class="abs center url" style="left:640px;top:2102px;width:260px;font-size:14px">www.velmorabeauty.com</div>
<div class="divider" style="left:680px;top:2135px;width:178px"></div>

<div class="abs center follow">Follow Us</div>
<div class="social" style="left:687px"></div>
<div class="social" style="left:748px"></div>
<div class="social" style="left:813px"></div>
<div class="abs center handle">@velmorabeautyofficial</div>

<div class="abs refund"><b>PLEASE NOTE:</b><br>ONCE THIS PRODUCT IS OPENED,<br>IT IS NOT REFUNDABLE</div>

</body>
</html>
```